Business Card Design (NEW FILES)

ATTENTION: New vector files are available. Please update your design to reflect/use the new (better resolution) logo images.

Seeking a unique and professional business card design for a commercial drone photography/videography business. The layout should feature
the logo (attached) and include the following information:
Owen Tarrick
614-502-7738
www.skylarkreelworks.example
NRD Certified Remote Pilot

Owen Tarrick

```html
<!DOCTYPE html>
<html lang="en">
<head>
<meta charset="utf-8">
<title>Skylark Reelworks — Business Card</title>
<link href="https://fonts.googleapis.com/css2?family=Open+Sans:wght@400;600;700;800&display=swap" rel="stylesheet">
<style>
  :root {
    --backdrop: #232323;
    --card: #f4f4f4;
    --navy: #181a48;
    --orange: #e5884f;
  }
  * { box-sizing: border-box; margin: 0; padding: 0; }
  html, body {
    width: 1200px; height: 780px; overflow: hidden;
    background: var(--backdrop);
    font-family: "Open Sans", Arial, sans-serif;
  }
  .sheet {
    width: 1200px; height: 780px;
    display: flex; align-items: center; justify-content: center; gap: 40px;
  }
  .card {
    position: relative;
    width: 560px; height: 320px;
    background: var(--card);
    border-radius: 18px;
    overflow: hidden;
  }
  /* wordmark */
  .wordmark {
    display: flex; align-items: center; gap: 10px;
    color: var(--navy); font-weight: 700; line-height: 1.05;
  }
  .wordmark-dot {
    flex: none; border-radius: 50%; background: var(--orange);
  }
  /* front */
  .front .wordmark { position: absolute; left: 36px; top: 62px; font-size: 28px; }
  .front .wordmark-dot { width: 26px; height: 26px; }
  .divider {
    position: absolute; left: 292px; top: 46px;
    width: 2px; height: 200px; background: var(--orange);
  }
  .details { position: absolute; left: 316px; top: 52px; color: var(--navy); }
  .person-name { font-size: 30px; font-weight: 800; line-height: 1.1; }
  .person-name .given { color: var(--orange); }
  .person-role { font-size: 14px; font-weight: 600; margin-bottom: 10px; }
  .credentials { font-size: 13px; font-weight: 600; line-height: 1.4; margin-bottom: 10px; }
  .contact-list { list-style: none; font-size: 13px; font-weight: 600; line-height: 1.7; }
  .contact-list li { display: flex; align-items: center; gap: 8px; white-space: nowrap; }
  .contact-list svg { width: 13px; height: 13px; flex: none; fill: var(--orange); }
  .band { position: absolute; bottom: 0; height: 28px; }
  .band-orange { left: 0; width: 48%; background: var(--orange); }
  .band-navy { right: 0; width: 52%; background: var(--navy); }
  /* back */
  .back { display: flex; align-items: center; justify-content: center; }
  .back .wordmark { font-size: 44px; gap: 16px; }
  .back .wordmark-dot { width: 40px; height: 40px; }
</style>
</head>
<body>
<main class="sheet">
  <section class="card front" aria-label="Card front">
    <div class="wordmark"><span class="wordmark-dot"></span><span>Skylark<br>Reelworks</span></div>
    <div class="divider"></div>
    <div class="details">
      <h1 class="person-name"><span class="given">Owen</span> Tarrick</h1>
      <p class="person-role">Owner</p>
      <p class="credentials">NRD Certified Remote Pilot<br>Fully Insured</p>
      <ul class="contact-list">
        <li><svg viewBox="0 0 24 24" aria-hidden="true"><path d="M6.6 10.8a15 15 0 0 0 6.6 6.6l2.2-2.2a1 1 0 0 1 1-.25 11.4 11.4 0 0 0 3.6.57 1 1 0 0 1 1 1V20a1 1 0 0 1-1 1A17 17 0 0 1 3 4a1 1 0 0 1 1-1h3.5a1 1 0 0 1 1 1c0 1.25.2 2.45.57 3.57a1 1 0 0 1-.25 1z"/></svg>614-502-7738</li>
        <li><svg viewBox="0 0 24 24" aria-hidden="true"><path d="M12 2a10 10 0 1 0 0 20 10 10 0 0 0 0-20zm6.9 6h-3a15.6 15.6 0 0 0-1.4-3.6A8 8 0 0 1 18.9 8zM12 4a14 14 0 0 1 1.9 4h-3.8A14 14 0 0 1 12 4zM4.3 14a8 8 0 0 1 0-4h3.4a16 16 0 0 0 0 4zm.8 2h3a15.6 15.6 0 0 0 1.4 3.6A8 8 0 0 1 5.1 16zm3-8h-3a8 8 0 0 1 4.4-3.6A15.6 15.6 0 0 0 8.1 8zM12 20a14 14 0 0 1-1.9-4h3.8A14 14 0 0 1 12 20zm2.3-6H9.7a14.7 14.7 0 0 1 0-4h4.6a14.7 14.7 0 0 1 0 4zm.2 5.6a15.6 15.6 0 0 0 1.4-3.6h3a8 8 0 0 1-4.4 3.6zm1.8-5.6a16 16 0 0 0 0-4h3.4a8 8 0 0 1 0 4z"/></svg>www.skylarkreelworks.example</li>
        <li><svg viewBox="0 0 24 24" aria-hidden="true"><path d="M3 5h18a1 1 0 0 1 1 1v12a1 1 0 0 1-1 1H3a1 1 0 0 1-1-1V6a1 1 0 0 1 1-1zm9 7.5L4 7.2V17h16V7.2z"/></svg>info@skylarkreelworks.example</li>
      </ul>
    </div>
    <div class="band band-orange"></div>
    <div class="band band-navy"></div>
  </section>

  <section class="card back" aria-label="Card back">
    <div class="wordmark"><span class="wordmark-dot"></span><span>Skylark<br>Reelworks</span></div>
  </section>
</main>
</body>
</html>
```